Health Spectrum and Energy Slides

Create beautiful and facinating PowerPoint slides that inspire and motivate

Target Market(s)

Clients looking for strategic breakthroughs and transformation

Industry/Entity Type

Health

Requirements
Must have
• Beautiful, heartfelt and fascinating graphics.
Nice to have
• Award winning designs.

```html
<!DOCTYPE html>
<html lang="en">
<head>
<meta charset="utf-8">
<title>Health Spectrum and Energy Slides</title>
<link rel="stylesheet" href="https://fonts.googleapis.com/css2?family=Open+Sans:wght@400;600;700&family=Arimo:wght@400&display=swap">
<style>
  :root {
    --page: #e9e6e1;
    --ink-dark: #1e1e1e;
    --ink-light: #ffffff;
    --battery: #ffffff;
    --charge-green: #39b54a;
    --drain-red: #e0262b;
    --plate: #f2f2f2;
    --plate-edge: #bdbdbd;
    --line: rgba(255,255,255,0.8);
  }
  * { box-sizing: border-box; margin: 0; padding: 0; }
  html, body { width: 1200px; height: 675px; overflow: hidden; }
  body {
    background: var(--page);
    font-family: "Open Sans", sans-serif;
  }
  .deck {
    position: absolute;
    left: 33px; top: 13px;
    display: grid;
    grid-template-columns: repeat(3, 370px);
    grid-template-rows: repeat(3, 208px);
    gap: 12px;
  }
  .slide {
    position: relative;
    width: 370px; height: 208px;
    overflow: hidden;
    box-shadow: 0 3px 8px rgba(0,0,0,0.25);
  }
  .photo { position: absolute; inset: 0; }
  .layer { position: absolute; }

  /* 1 — portals */
  .photo--doorway { background: linear-gradient(100deg, #f4f4f4 0%, #dcdcdc 45%, #a9a9a9 70%, #6b6b6b 100%); }
  .portal-text {
    left: 14px; top: 12px; width: 210px;
    font-size: 6.4px; line-height: 1.45; color: var(--ink-dark);
  }
  .portal-text p { margin-bottom: 3px; }
  .portal-text b { font-weight: 700; }

  /* 2 — charge me up */
  .photo--windfarm { background: linear-gradient(180deg, #f0a35a 0%, #6b87b8 30%, #2d5fa6 55%, #4f8a3a 75%, #2f6b2a 100%); }
  .charge-title { right: 14px; top: 8px; text-align: right; color: var(--ink-light); }
  .charge-title h2 { font-size: 21px; font-weight: 700; letter-spacing: 0.5px; }
  .charge-title p { font-size: 9px; font-weight: 600; letter-spacing: 0.6px; }
  .charge-list { font-size: 5.6px; line-height: 1.4; color: var(--ink-light); font-weight: 600; }
  .charge-list--recharge { left: 12px; top: 14px; }
  .charge-list--exhaust { right: 14px; top: 78px; text-align: right; }
  .charge-list h3 { font-size: 6.5px; font-weight: 700; }
  .charge-footer { left: 12px; bottom: 10px; font-size: 5.6px; color: var(--ink-light); font-weight: 600; }
  .batteries { left: 84px; top: 62px; }

  /* 3 — mirror */
  .photo--mirror { background: linear-gradient(90deg, #2a2a2a 0%, #5a5a5a 40%, #3d3d3d 70%, #202020 100%); }
  .mirror-text {
    left: 168px; top: 72px; width: 180px;
    font-size: 9px; line-height: 1.4; color: var(--ink-light);
  }
  .mirror-text p + p { margin-top: 8px; }

  /* 4 — maze head */
  .photo--maze-ground { background: #0d0d0d; }
  .photo--maze {
    left: 190px; top: 30px; right: 0; bottom: 0;
    background:
      radial-gradient(ellipse at 35% 55%, #8a8a8a 0%, #5a5a5a 30%, rgba(40,40,40,0) 70%),
      linear-gradient(120deg, #1a1a1a 0%, #3c3c3c 45%, #6e6e6e 70%, #4a4a4a 100%);
    border-top-left-radius: 60px;
  }

  /* 5 — dandelion */
  .photo--dandelion { background: linear-gradient(160deg, #e9ebe6 0%, #cfd5c4 40%, #a9bf88 60%, #e49a58 85%, #d8743c 100%); }
  .fear-word {
    position: absolute; font-size: 8px; font-style: italic; color: var(--ink-light);
    text-shadow: 0 0 3px rgba(0,0,0,0.55);
  }

  /* 6 — spectrum */
  .photo--spectrum { background: linear-gradient(180deg, #f4d54a 0%, #f0b23a 25%, #b0c9d8 45%, #2e8bc5 55%, #1b5b93 80%, #0d3660 100%); }
  .spectrum-photo-right { position: absolute; right: 0; top: 0; bottom: 0; width: 150px; background: linear-gradient(180deg, #7b7b7b 0%, #4a4a4a 60%, #333 100%); }
  .spectrum-title { font-size: 7px; font-weight: 700; line-height: 1.2; color: var(--ink-dark); }
  .spectrum-title--left { left: 12px; top: 10px; }
  .spectrum-title--right { right: 10px; top: 10px; text-align: right; color: var(--ink-light); }
  .spectrum-label { font-size: 4.8px; line-height: 1.3; color: var(--ink-light); width: 62px; }
  .spectrum-label--dark { color: #333; }
  .spectrum-lines { left: 0; top: 0; }

  /* 7 — restaurant */
  .photo--restaurant { background: linear-gradient(180deg, #7a4a22 0%, #b8773c 35%, #e0a866 60%, #c9925a 80%, #a77442 100%); }
  .restaurant-title {
    left: 18px; top: 14px; color: var(--ink-light);
    font-size: 11px; font-weight: 700; line-height: 1.35;
    text-shadow: 0 1px 3px rgba(0,0,0,0.5);
  }
  .plates { left: 0; top: 0; }
  .plates text { font-family: "Open Sans", sans-serif; font-size: 5.4px; fill: #333; text-anchor: middle; }

  /* 8 — course correction */
  .photo--sea { background: linear-gradient(180deg, #1d2b36 0%, #53707f 35%, #8fa7ad 50%, #2c3d46 70%, #15212a 100%); }
  .course-title {
    left: 0; right: 0; top: 26px; text-align: center;
    color: var(--ink-light); font-size: 14px; font-weight: 700; letter-spacing: 0.5px;
  }
  .course-text {
    left: 0; right: 0; bottom: 22px; text-align: center;
    color: var(--ink-light); font-size: 8.5px; line-height: 1.45;
  }

  /* 9 — be the sky */
  .photo--sky { background: linear-gradient(180deg, #0c0f2c 0%, #1b1f4a 40%, #3a2d68 62%, #b2457d 82%, #f08a3a 100%); }
  .sky-title {
    left: 0; right: 0; top: 48px; text-align: center;
    font-family: "Arimo", sans-serif; color: var(--ink-light); font-size: 15px; letter-spacing: 0.5px;
  }
  .sky-text {
    left: 0; right: 0; top: 84px; text-align: center;
    font-family: "Arimo", sans-serif; color: var(--ink-light); font-size: 12px; line-height: 1.5;
  }
</style>
</head>
<body>
<main class="deck">

  <section class="slide slide--portals">
    <div class="photo photo--doorway" role="img" aria-label="Soft light falling through an open doorway in a bright white room"></div>
    <div class="layer portal-text">
      <p>These are the portals that enhance your awareness and compassion so you can meet your best highest self.</p>
      <p><b>One:</b> You are not alone. Send out your thoughts and feelings. You will find predictable and unpredictable pieces.</p>
      <p><b>Two:</b> Everything is impermanent. This is a temporary state.</p>
      <p><b>Three:</b> Observe, name and express your dis-ease and dis-stress. You are not the emotion.</p>
      <p><b>Four:</b> Quality questions create a quality experience. How could you ever create it with this challenge?</p>
      <p><b>Five:</b> If you could choose anything, what would your heart choose?</p>
      <p>Live your Heartfelt Desire <b>"AS IF"</b> you are already there. Love &amp; Gratitude!</p>
    </div>
  </section>

  <section class="slide slide--charge">
    <div class="photo photo--windfarm" role="img" aria-label="Wind turbines over green marshland and a river at sunset"></div>
    <div class="layer charge-list charge-list--recharge">
      <h3>RECHARGE</h3>
      Rest &amp; Recharge<br>Breathe Deeply<br>Nature Walk<br>Gratitude<br>Joyful Movement<br>Heartfelt Goals<br>Connection<br>Laughter<br>Positive Support<br>Sleep Well
    </div>
    <div class="layer charge-title">
      <h2>CHARGE ME UP!</h2>
      <p>ENERGY USE AND RETENTION</p>
    </div>
    <svg class="layer batteries" width="162" height="62" viewBox="-12 0 162 62" aria-hidden="true">
      <line x1="-5" y1="58" x2="-5" y2="8" stroke="var(--charge-green)" stroke-width="3"/>
      <polygon points="-10,9 -5,0 0,9" fill="var(--charge-green)"/>
      <g fill="none" stroke="var(--battery)" stroke-width="3">
        <rect x="6" y="8" width="26" height="48"/><rect x="40" y="8" width="26" height="48"/>
        <rect x="74" y="8" width="26" height="48"/><rect x="108" y="8" width="26" height="48"/>
      </g>
      <g fill="var(--battery)">
        <rect x="14" y="3" width="10" height="5"/><rect x="48" y="3" width="10" height="5"/>
        <rect x="82" y="3" width="10" height="5"/><rect x="116" y="3" width="10" height="5"/>
        <rect x="11" y="13" width="16" height="8"/><rect x="11" y="24" width="16" height="8"/><rect x="11" y="35" width="16" height="8"/><rect x="11" y="46" width="16" height="6"/>
        <rect x="45" y="24" width="16" height="8"/><rect x="45" y="35" width="16" height="8"/><rect x="45" y="46" width="16" height="6"/>
        <rect x="79" y="35" width="16" height="8"/><rect x="79" y="46" width="16" height="6"/>
        <rect x="113" y="46" width="16" height="6"/>
      </g>
      <line x1="143" y1="4" x2="143" y2="52" stroke="var(--drain-red)" stroke-width="3"/>
      <polygon points="138,50 143,59 148,50" fill="var(--drain-red)"/>
    </svg>
    <div class="layer charge-list charge-list--exhaust">
      <h3>EXHAUST</h3>
      Overthinking<br>People Pleasing<br>Fear &amp; Worry<br>Self Doubt<br>Negative Self Talk<br>Victim, Why Me
    </div>
    <div class="layer charge-footer">Awareness · Clear Boundaries · Living on Purpose · Present Moment</div>
  </section>

  <section class="slide slide--mirror">
    <div class="photo photo--mirror" role="img" aria-label="Black and white scene of an older man looking at his younger reflection in a bathroom mirror"></div>
    <div class="layer mirror-text">
      <p>We don't see the truth. We see what we believe.</p>
      <p>When you change your beliefs you change what you see, feel and hear so your reflection in the world changes.</p>
    </div>
  </section>

  <section class="slide slide--maze">
    <div class="photo photo--maze-ground"></div>
    <div class="layer photo--maze" role="img" aria-label="Monochrome profile of a head opening into a stone maze, lit from the right on a black background"></div>
  </section>

  <section class="slide slide--dandelion">
    <div class="photo photo--dandelion" role="img" aria-label="Red-haired child blowing dandelion seeds in a soft sunlit meadow"></div>
    <span class="fear-word" style="left:30px;top:22px;">Not Good Enough</span>
    <span class="fear-word" style="left:110px;top:30px;">Unlovable</span>
    <span class="fear-word" style="left:190px;top:24px;">Hopeless</span>
    <span class="fear-word" style="left:20px;top:80px;">Fake</span>
    <span class="fear-word" style="left:58px;top:72px;">Give Up</span>
    <span class="fear-word" style="left:150px;top:66px;">Why Me</span>
    <span class="fear-word" style="left:40px;top:112px;">Failure</span>
    <span class="fear-word" style="left:100px;top:106px;">Fear</span>
    <span class="fear-word" style="left:160px;top:100px;">Sad</span>
    <span class="fear-word" style="left:130px;top:130px;">Anxiety</span>
    <span class="fear-word" style="left:200px;top:128px;">Anger</span>
    <span class="fear-word" style="left:85px;top:150px;">Hate</span>
    <span class="fear-word" style="left:120px;top:172px;">Loss</span>
  </section>

  <section class="slide slide--spectrum">
    <div class="photo photo--spectrum" role="img" aria-label="Split landscape of sunlit sky over sea with a tree whose roots reach underwater"></div>
    <div class="spectrum-photo-right" role="img" aria-label="Grey toned half of the landscape"></div>
    <div class="layer spectrum-title spectrum-title--left">OPTIMAL HEALTH TO<br>DEATH<br>MALADAPTIVE<br>DIS-STRESS<br>REACTION<br>SPECTRUM</div>
    <div class="layer spectrum-title spectrum-title--right">TRANSFORMATION<br>TO DEATH<br>ADAPTIVE<br>RESPONSE<br>SPECTRUM</div>
    <svg class="layer spectrum-lines" width="370" height="208" viewBox="0 0 370 208" aria-hidden="true">
      <path d="M150 30 C170 70 150 110 175 140 C190 160 185 180 200 200" fill="none" stroke="var(--line)" stroke-width="0.8"/>
      <line x1="235" y1="80" x2="235" y2="195" stroke="var(--line)" stroke-width="0.6"/>
      <line x1="90" y1="168" x2="340" y2="168" stroke="var(--line)" stroke-width="0.6"/>
    </svg>
    <div class="layer spectrum-label spectrum-label--dark" style="left:112px;top:40px;">Optimal Health Emotional, Spiritual &amp; Physical</div>
    <div class="layer spectrum-label spectrum-label--dark" style="left:106px;top:72px;">Subconscious Stress</div>
    <div class="layer spectrum-label spectrum-label--dark" style="left:95px;top:96px;">Outside the Zone &amp; Comfort Zone</div>
    <div class="layer spectrum-label" style="left:60px;top:130px;">Chronic Stress &amp; Dis-Ease Zone</div>
    <div class="layer spectrum-label" style="left:70px;top:150px;">Health Physical, Emotional, Structural</div>
    <div class="layer spectrum-label" style="left:240px;top:92px;">Transformation Conscious Heartfelt Choice &amp; Action</div>
    <div class="layer spectrum-label" style="left:240px;top:122px;">Change Awareness</div>
    <div class="layer spectrum-label" style="left:240px;top:140px;">Resilience</div>
    <div class="layer spectrum-label" style="left:240px;top:152px;">Reactive Habits, Unhealthy Patterns</div>
    <div class="layer spectrum-label" style="left:240px;top:178px;">Death Physical, Emotional, Structural</div>
  </section>

  <section class="slide slide--restaurant">
    <div class="photo photo--restaurant" role="img" aria-label="Blurred warm restaurant interior above a wooden table"></div>
    <div class="layer restaurant-title">YOUR RESTAURANT:<br>YOU CAN EAT ANYTHING THAT YOU WANT AT</div>
    <svg class="layer plates" width="370" height="208" viewBox="0 0 370 208" aria-hidden="true">
      <g fill="var(--plate)" stroke="var(--plate-edge)" stroke-width="0.8">
        <ellipse cx="50" cy="64" rx="30" ry="11"/>
        <ellipse cx="46" cy="112" rx="28" ry="10"/>
        <ellipse cx="48" cy="142" rx="30" ry="11"/>
        <ellipse cx="112" cy="134" rx="30" ry="11"/>
        <ellipse cx="118" cy="170" rx="30" ry="11"/>
        <ellipse cx="196" cy="160" rx="30" ry="11"/>
        <ellipse cx="310" cy="130" rx="32" ry="11"/>
        <ellipse cx="276" cy="186" rx="30" ry="11"/>
      </g>
      <text x="50" y="63">Least</text><text x="50" y="69">Favorite Food</text>
      <text x="46" y="111">Heartfelt</text><text x="46" y="117">Desire</text>
      <text x="48" y="141">Uncomfortable</text><text x="48" y="147">Emotions</text>
      <text x="112" y="133">Pleasurable</text><text x="112" y="139">Emotions</text>
      <text x="118" y="169">Painful</text><text x="118" y="175">Emotions</text>
      <text x="196" y="159">Neutral</text><text x="196" y="165">Emotions</text>
      <text x="310" y="129">Favorite</text><text x="310" y="135">Food</text>
      <text x="276" y="185">Neutral</text><text x="276" y="191">Food</text>
    </svg>
  </section>

  <section class="slide slide--course">
    <div class="photo photo--sea" role="img" aria-label="Sailboat on rough water under dramatic storm clouds"></div>
    <h2 class="layer course-title">COURSE CORRECTION</h2>
    <p class="layer course-text">When the seas turn how do you stay on course?<br>Who do you become in the face of fear and uncertainty?</p>
  </section>

  <section class="slide slide--sky">
    <div class="photo photo--sky" role="img" aria-label="Starry night sky fading to a purple and orange horizon"></div>
    <h2 class="layer sky-title">BE THE SKY</h2>
    <p class="layer sky-text">The Sky has room for all types of<br>changing weather and all the seasons.</p>
  </section>

</main>
</body>
</html>
```